Talvenna Capital LLC

Need Professional Business cards for New Investment Fund

Target Market(s)

High Quality investors

Industry/Entity Type

Financial

Contact Information for Business Card

Phone Number +1 555 284 6190
Name Lukas Varenko
Title Fund Manager
email lv@FundTalvenna.com
Website www.FundTalvenna.com

Colors

Designer to choose colors to be used in the design.

Requirements
Must have
• Must have our Logo and all of the above. Must be made so lettering and loge can be raised

```html
<!DOCTYPE html>
<html lang="en">
<head>
<meta charset="utf-8">
<title>Talvenna Capital LLC – Business Card</title>
<link href="https://fonts.googleapis.com/css2?family=Arimo:wght@400;700&display=swap" rel="stylesheet">
<style>
  :root {
    --backdrop: #3a3a3a;
    --brand-green: #5cb947;
    --ink-dark: #3f4a41;
    --card-white: #ffffff;
    --text-muted: #4a514b;
  }
  * { box-sizing: border-box; margin: 0; padding: 0; }
  html, body {
    width: 1200px;
    height: 900px;
    overflow: hidden;
    background: var(--backdrop);
    font-family: "Arimo", Arial, sans-serif;
  }
  .stage {
    position: relative;
    width: 1200px;
    height: 900px;
  }
  .card {
    position: absolute;
    left: 290px;
    width: 620px;
    height: 354px;
    border-radius: 2px;
  }
  .card--front {
    top: 56px;
    background: var(--brand-green);
    display: flex;
    align-items: center;
    justify-content: center;
  }
  .card--back {
    top: 452px;
    background: var(--card-white);
  }
  .brand-name {
    display: flex;
    align-items: center;
    gap: 14px;
    font-weight: 700;
    letter-spacing: 3px;
    text-transform: uppercase;
    white-space: nowrap;
  }
  .brand-name__mark {
    display: block;
    width: 22px;
    height: 22px;
    flex: none;
  }
  .card--front .brand-name {
    color: var(--card-white);
    font-size: 44px;
  }
  .card--front .brand-name__mark { background: var(--card-white); }
  .card--back .brand-name {
    position: absolute;
    left: 34px;
    top: 162px;
    color: var(--ink-dark);
    font-size: 26px;
    gap: 12px;
    letter-spacing: 2px;
  }
  .card--back .brand-name__mark {
    background: var(--brand-green);
    width: 16px;
    height: 16px;
  }
  .divider {
    position: absolute;
    left: 272px;
    top: 36px;
    width: 3px;
    height: 282px;
    background: var(--brand-green);
  }
  .contact {
    position: absolute;
    left: 306px;
    top: 76px;
    color: var(--ink-dark);
  }
  .contact__name {
    font-size: 24px;
    font-weight: 700;
    letter-spacing: 0.5px;
  }
  .contact__title {
    font-size: 17px;
    color: var(--text-muted);
    margin-top: 2px;
    margin-bottom: 22px;
  }
  .contact__list { list-style: none; }
  .contact__item {
    display: flex;
    align-items: center;
    gap: 12px;
    font-size: 20px;
    color: var(--text-muted);
    margin-bottom: 14px;
    white-space: nowrap;
  }
  .contact__icon {
    width: 20px;
    height: 20px;
    flex: none;
    fill: var(--brand-green);
  }
</style>
</head>
<body>
<main class="stage">
  <section class="card card--front" aria-label="Card front">
    <div class="brand-name"><span class="brand-name__mark"></span>Talvenna</div>
  </section>

  <section class="card card--back" aria-label="Card back">
    <div class="brand-name"><span class="brand-name__mark"></span>Talvenna</div>
    <div class="divider"></div>
    <div class="contact">
      <p class="contact__name">Lukas Varenko</p>
      <p class="contact__title">Fund Manager</p>
      <ul class="contact__list">
        <li class="contact__item">
          <svg class="contact__icon" viewBox="0 0 24 24" aria-hidden="true"><path d="M6.6 10.8a15.1 15.1 0 0 0 6.6 6.6l2.2-2.2a1 1 0 0 1 1-.25 11.4 11.4 0 0 0 3.6.57 1 1 0 0 1 1 1V20a1 1 0 0 1-1 1A17 17 0 0 1 3 4a1 1 0 0 1 1-1h3.5a1 1 0 0 1 1 1c0 1.250.2 2.45.57 3.6a1 1 0 0 1-.25 1z"/></svg>
          +1 555 284 6190
        </li>
        <li class="contact__item">
          <svg class="contact__icon" viewBox="0 0 24 24" aria-hidden="true"><path d="M2 5h20v14H2z"/><path d="M2 5l10 8 10-8" fill="none" stroke="#fff" stroke-width="1.8"/></svg>
          lv@FundTalvenna.com
        </li>
        <li class="contact__item">
          <svg class="contact__icon" viewBox="0 0 24 24" aria-hidden="true"><circle cx="12" cy="12" r="10"/><path d="M2 12h20M12 2c3 3 3 17 0 20M12 2c-3 3-3 17 0 20" fill="none" stroke="#fff" stroke-width="1.4"/></svg>
          www.FundTalvenna.com
        </li>
      </ul>
    </div>
  </section>
</main>
</body>
</html>
```